Design letter head and business card

Hello,

you should design a business card and letter paper for Kranichflug Marketing. In German we write this word with K insteat of C.

Company does not have a logo. But in general, we write Kranichflug Marketing in 2 lines.
First line red: KRANICHFLUG
Second line gray: MARKETING

Red (or wine red) and Gray / Black are our favorite colors.

Company slogan: "Fresh Ground Online Marketing".

Company offers SEO, SEM, SEA, AdWords, Conversion Optimization, Online Markting Consulting ...

The website is old, please do not use this as base for your task.

German letter paper sizes:
Viawable Dimensions : 210 x 297 mm
Needed file dimensions: 212 x 299 mm

Informations to include:

Address:
Kranichflug Marketing GmbH
Lindenweg 23
71592 Weinstadt
Germany

Geschäftsführer | CEO: Bernhard Olzner

Phone: +49 (0) 7151 846 27 05

Fax: +49 (0) 7151 846 27 88

Mail: info@kranichflug-beispiel.de

Web: www.kranichflug-beispiel.de

Amtsgericht Suttgart, HRB 537264

Bank: Rosenauer Bank
IBAN: DE827315480900XXXXXXXX
BIC: GENODES1RSQ

Thanks

Bernhard

Target Market(s)

People who likes to win the online marketing game.

Industry/Entity Type

Business

Contact Information for Business Card

Here is the personal text on the card:

Name:
Bernhard Olzner

Title:
Geschäftsführer | CEO

Address:
Kranichflug Marketing GmbH
Lindenweg 23
71592 Weinstadt
Germany

Phone:
+49 (0) 7151 846 27 05

Fax:
+49 (0) 7151 846 27 88

Mail:
olzner@kranichflug-beispiel.de

Web:
www.kranichflug-beispiel.de

Business Card:
Viewable Dimensions: 85 x 55 mm
Needed file dimensions: 87 x 57mm

Font styles to use
Sans Serif

Requirements
Nice to have
• It would be great to see the dynamics of a helicopter.

```html
<!DOCTYPE html>
<html lang="de">
<head>
<meta charset="utf-8">
<title>Kranichflug Marketing – Visitenkarte Rückseite</title>
<link rel="stylesheet" href="https://fonts.googleapis.com/css2?family=Oswald:wght@300;400&amp;family=Economica:wght@400;700&amp;display=swap">
<style>
  :root {
    --bg: #d1d2d4;
    --card-top: #a6a7aa;
    --wine: #8e1f22;
    --ink: #2b2b2b;
    --mail-text: #ece6e0;
  }
  html, body {
    margin: 0;
    padding: 0;
    width: 1200px;
    height: 667px;
    overflow: hidden;
    background: var(--bg);
  }
  .card {
    position: relative;
    width: 1200px;
    height: 667px;
    font-family: "Economica", "Oswald", sans-serif;
    color: var(--ink);
    text-align: center;
  }
  .top-band {
    position: absolute;
    left: 414px;
    top: 0;
    width: 371px;
    height: 64px;
    background: var(--card-top);
  }
  .person-name {
    position: absolute;
    top: 128px;
    left: 0;
    width: 1200px;
    margin: 0;
    font-family: "Oswald", sans-serif;
    font-weight: 400;
    font-size: 46px;
    line-height: 60px;
    color: var(--wine);
    transform: scaleX(0.88);
  }
  .person-title {
    position: absolute;
    top: 188px;
    left: 0;
    width: 1200px;
    margin: 0;
    font-size: 33px;
    line-height: 38px;
  }
  .address {
    position: absolute;
    top: 296px;
    left: 0;
    width: 1200px;
    margin: 0;
    font-style: normal;
    font-size: 38px;
    line-height: 43px;
  }
  .contact {
    position: absolute;
    top: 456px;
    left: 0;
    width: 1200px;
    margin: 0;
    font-size: 38px;
    line-height: 43px;
  }
  .mail-band {
    position: absolute;
    left: 414px;
    top: 567px;
    width: 371px;
    height: 100px;
    background: var(--wine);
  }
  .mail-address {
    position: absolute;
    top: 582px;
    left: 414px;
    width: 371px;
    margin: 0;
    font-weight: 700;
    font-size: 34px;
    line-height: 42px;
    color: var(--mail-text);
  }
</style>
</head>
<body>
  <main class="card">
    <div class="top-band"></div>
    <h1 class="person-name">Bernhard Olzner</h1>
    <p class="person-title">Geschäftsführer | CEO</p>
    <address class="address">
      Kranichflug Marketing GmbH,<br>
      Lindenweg 23,<br>
      71592 Weinstadt, Germany
    </address>
    <p class="contact">
      Phone: +49 (0) 7151 846 27 05<br>
      Fax: +49 (0) 7151 846 27 88
    </p>
    <div class="mail-band"></div>
    <p class="mail-address">info@kranichflug-beispiel.de</p>
  </main>
</body>
</html>
```